Velvet Lantern rebranding my business with a new business card

I have my new logo and now I need a refresher on my business cards. I really want something fun and fresh. I like black background or anything to make the color pop.
Logo
Name: Velvet Lantern
Contact Info as stated below:
Mira Pellow
555-013-4762
Logo
Name: Velvet Lantern
Mira Pellow
555-013-4762
fb.me/VelvetLanternbyMira
Instagram: @VelvetLanternbyMira

Industry/Entity Type

Business

Contact Information for Business Card

double-sided. Logo on one side. Contact info on the other.

Requirements
Must have
• Logo
• Name: Velvet Lantern
• Contact Info as stated below:
• Mira Pellow
• 555-013-4762
• fb.me/VelvetLanternbyMira
• fb.me/VelvetLanternbyMira

```html
<!DOCTYPE html>
<html lang="en">
<head>
<meta charset="utf-8">
<title>Velvet Lantern — Business Card</title>
<link rel="stylesheet" href="https://fonts.googleapis.com/css2?family=Oswald:wght@500&family=Roboto+Condensed:wght@400&display=swap">
<style>
  :root {
    --stage: #ece8e6;
    --card-white: #ffffff;
    --purple: #b84ad3;
    --rose: #f3a7a9;
    --blush: #fde3e8;
    --ink: #1a1a1a;
    --ring: #f2a9bd;
    --shadow: rgba(40, 20, 30, 0.22);
  }
  * { box-sizing: border-box; margin: 0; padding: 0; }
  html, body { width: 1200px; height: 911px; overflow: hidden; }
  body {
    background: var(--stage);
    font-family: "Roboto Condensed", sans-serif;
    color: var(--ink);
    position: relative;
  }
  .card {
    position: absolute;
    left: 280px;
    width: 640px;
    height: 366px;
    border-radius: 22px;
    overflow: hidden;
    box-shadow: 0 10px 28px var(--shadow);
  }
  .card--front { top: 70px; background: linear-gradient(100deg, var(--purple) 0%, var(--rose) 52%, var(--blush) 100%); }
  .card--back { top: 476px; background: var(--card-white); }

  .front-corner {
    position: absolute;
    right: -120px; top: -160px;
    width: 420px; height: 420px;
    border-radius: 50%;
    background: var(--ink);
  }
  .logo-disc {
    position: absolute;
    right: 58px; top: 30px;
    width: 300px; height: 300px;
    border-radius: 50%;
    background: var(--card-white);
    border: 3px solid var(--ring);
    box-shadow: 0 0 0 6px var(--card-white), 0 0 0 8px var(--ring), 0 6px 16px var(--shadow);
    display: flex; align-items: center; justify-content: center;
  }
  .brand {
    display: flex; align-items: center; gap: 10px;
    font-family: "Roboto Condensed", sans-serif;
    font-weight: 400;
    font-size: 30px;
    color: var(--ink);
  }
  .brand-dot { width: 16px; height: 16px; border-radius: 50%; background: var(--ring); flex: none; }

  .contact {
    position: absolute;
    left: 44px; bottom: 46px;
  }
  .contact-name {
    font-family: "Oswald", sans-serif;
    font-weight: 500;
    font-size: 27px;
    letter-spacing: 0.5px;
    margin-bottom: 14px;
  }
  .contact-line {
    display: flex; align-items: center; gap: 10px;
    font-size: 17px;
    line-height: 26px;
    color: #2b2b2b;
  }
  .contact-line svg { width: 14px; height: 14px; flex: none; }

  .back-url {
    position: absolute;
    left: 44px; top: 40px;
    font-size: 14px;
    letter-spacing: 7px;
    color: #444;
  }
  .back-logo {
    position: absolute;
    inset: 0;
    display: flex; align-items: center; justify-content: center;
  }
</style>
</head>
<body>
  <section class="card card--front" aria-label="Business card, contact side">
    <div class="front-corner"></div>
    <div class="logo-disc">
      <div class="brand"><span class="brand-dot"></span>Velvet Lantern</div>
    </div>
    <div class="contact">
      <p class="contact-name">MIRA PELLOW</p>
      <p class="contact-line">
        <svg viewBox="0 0 16 16" aria-hidden="true"><path d="M3 1.5l3 .5 1 3.5-2 1.2a8 8 0 0 0 4.3 4.3L10.5 9l3.5 1 .5 3c-.5 1.2-1.6 1.8-3 1.5C6.5 13.5 2.5 9.5 1.5 4.5 1.2 3.1 1.8 2 3 1.5z" fill="#1a1a1a"/></svg>
        555-013-4762
      </p>
      <p class="contact-line">
        <svg viewBox="0 0 16 16" aria-hidden="true"><circle cx="8" cy="8" r="6.5" fill="none" stroke="#1a1a1a" stroke-width="1.6"/><path d="M1.5 8h13M8 1.5c-2.4 2.8-2.4 10.2 0 13M8 1.5c2.4 2.8 2.4 10.2 0 13" fill="none" stroke="#1a1a1a" stroke-width="1.2"/></svg>
        www.velvetlantern.com
      </p>
      <p class="contact-line">
        <svg viewBox="0 0 16 16" aria-hidden="true"><rect x="2" y="2" width="12" height="12" rx="2" fill="#1a1a1a"/></svg>
        fb.me/VelvetLanternbyMira
      </p>
    </div>
  </section>

  <section class="card card--back" aria-label="Business card, logo side">
    <p class="back-url">www.velvetlantern.com</p>
    <div class="back-logo">
      <div class="brand"><span class="brand-dot"></span>Velvet Lantern</div>
    </div>
  </section>
</body>
</html>
```